Shopfront Graphics , front,side doors, small wall and mall entry.

New graphics retail store opening.

We are looking for a contemporary store front graphic that screams, Graphics, colour and ATTENTION.

The Fascia is approximately 3m high x 5 metres wide. We envisage a lightbox along the top and graphics continuing across the glass below.

We then have the side wall and graphics approximately 2.5m x 10m, and then second floor with glass and concrete.

Can we try a theme that partially covers all walls ..window frames and glass...Not overdone, but similar to the area covered in my demo pic of another store...Not just limited to the paint splash...your ideas...concepts?

Just to save all graphicos time at the initial concept stage,

Can we just stick to the front signage and the successful designer can just continue theme on other windows..
ORRRRRR..if you really want to impress and you have time....as before do the lot!
Just looking for the THEME layout at first.

Thanks
TM

Please see new front windows...do not follow this designers image, please ignore. But please note the front door now on Right hand side of front. 

We do have an interesting angle now, I would like minimal graphics now. Velmoria on light box above glass...but do need some theme.

I will place on here some more printed samples from our logo.

Note we need the TV screens to be seen  but some nice pattern/design to hold all the windows together!!

Thanks Tobias

OK we seem to be going the wrong way with splashes now..Too much and starting to look TOO colourful and TOO messy...I have attached some images that I took off Pixmorrow that are more in keeping with what I am looking for. I will also send you a rough sketch of an interior plan or "LOOK". 

The inside of the store is being professionally designed..White on white.. I am thinking of introducing one vibrant stripe.
Hope this helps with the "FEEL".....

Target Market(s)

This shop is a high street location with a lot of pedestrians.
The store is being designed as a fun collaborative store with seating and computer stations where anyone can come in and design, Photobooks, full colour T shirts, posters, Photogifts such as Mugs, Mouse mats, Canvas fine art pictures....

General atmosphere is FUN, entertaing and based on consumers wandering in, a bit like the ZENDRIL HALL experience.

We also make commercial signage, vehicle wraps, acrylic signs, photocopy and print banners. Regular signshop products.

Industry/Entity Type

Retail

Font styles to use
Sans Serif

Colors
9bcb3b
e34197
33a6d7

Requirements
Must have
• Our logo.
Lets concentrate on the main front window and light box with logo....see new updated files.
Velmoria, as designed by quillvane guys!!
Nice to have
• THe walls and windows should have a theme pattern, like the attached sign shop. I like that look with the full colour splash but we are very open to your ideas.
Should not have
• Pictures of CATS!

```html
<!DOCTYPE html>
<html lang="en">
<head>
<meta charset="utf-8">
<title>Velmoria – Shopfront Lightbox</title>
<link rel="stylesheet" href="https://fonts.googleapis.com/css2?family=Montserrat:wght@700&display=swap">
<style>
  :root {
    --canvas: #ffffff;
    --frame: #3a3a3a;
    --ink: #1b1b1b;
    --brand-green: #9bcb3b;
    --brand-pink: #e34197;
    --brand-blue: #33a6d7;
    --splash-red: #e2262f;
    --splash-yellow: #f6c21c;
    --splash-purple: #9b3fa5;
  }
  html, body {
    margin: 0;
    padding: 0;
    overflow: hidden;
    background: var(--canvas);
  }
  .lightbox {
    position: relative;
    width: 1200px;
    height: 722px;
    box-sizing: border-box;
    border: 2px solid var(--frame);
    background: var(--canvas);
    overflow: hidden;
  }
  .splash {
    position: absolute;
    opacity: 0.9;
  }
  .splash--top-left {
    left: 0; top: 0;
    width: 270px; height: 360px;
    border-radius: 0 60% 55% 40%;
    background: linear-gradient(160deg, var(--splash-red) 0%, var(--splash-yellow) 30%, var(--brand-blue) 55%, var(--splash-purple) 80%, rgba(255,255,255,0) 100%);
  }
  .splash--top-right {
    right: 0; top: 0;
    width: 320px; height: 310px;
    border-radius: 55% 0 35% 60%;
    background: linear-gradient(220deg, var(--splash-purple) 0%, var(--splash-yellow) 25%, var(--splash-red) 45%, var(--brand-green) 70%, rgba(255,255,255,0) 100%);
  }
  .splash--bottom-left {
    left: 0; bottom: 0;
    width: 290px; height: 285px;
    border-radius: 45% 60% 0 0;
    background: linear-gradient(30deg, var(--brand-blue) 0%, var(--splash-yellow) 30%, var(--splash-red) 50%, var(--brand-green) 75%, rgba(255,255,255,0) 100%);
  }
  .splash--bottom-right {
    right: 0; bottom: 0;
    width: 270px; height: 300px;
    border-radius: 60% 40% 0 0;
    background: linear-gradient(330deg, var(--splash-red) 0%, var(--brand-pink) 25%, var(--splash-yellow) 45%, var(--brand-blue) 70%, rgba(255,255,255,0) 100%);
  }
  .brand {
    position: absolute;
    left: 340px;
    top: 350px;
    display: flex;
    align-items: center;
    gap: 26px;
  }
  .brand__mark {
    width: 34px;
    height: 34px;
    background: var(--brand-pink);
  }
  .brand__name {
    margin: 0;
    font-family: "Montserrat", sans-serif;
    font-weight: 700;
    font-size: 112px;
    line-height: 1;
    letter-spacing: -2px;
    color: var(--ink);
  }
</style>
</head>
<body>
  <main class="lightbox">
    <div class="splash splash--top-left" role="img" aria-label="Colourful paint splash in red, yellow, blue and purple"></div>
    <div class="splash splash--top-right" role="img" aria-label="Colourful paint splash in green, red, yellow and purple"></div>
    <div class="splash splash--bottom-left" role="img" aria-label="Colourful paint splash in green, red, yellow and blue"></div>
    <div class="splash splash--bottom-right" role="img" aria-label="Colourful paint splash in red, pink, yellow and blue"></div>

    <div class="brand">
      <span class="brand__mark" aria-hidden="true"></span>
      <h1 class="brand__name">Velmoria</h1>
    </div>
  </main>
</body>
</html>
```